cryotherapy business . Whole Body Cryotherapy, Localised Cryotherapy, Cryofacials

Need home page plus services, about, pricing, online booking, contact and blog page

I want something slick, hip and professional. Our studio colours are duck egg blue, white and grey

I would also like a social media scroll at the bottom of every page

I will upload some web designs that I like the look of

Target Market(s)

Men and Women 25-45

Industry/Entity Type

Health And Wellness

Coding

Coded - Design and coding required

Number of Pages Required

5+ page

Font styles to use
Serif
Sans Serif

Requirements
Must have
• Must be eye catching and easy to navigate
Nice to have
• animation
Should not have
• Not sure what the site should not have. I am fairly open to ideas as this is a brand new business.

```html
<!DOCTYPE html>
<html lang="en">
<head>
<meta charset="utf-8">
<title>Frostline — Cryotherapy Studio</title>
<link href="https://fonts.googleapis.com/css2?family=Lato:wght@300;400;700;900&display=swap" rel="stylesheet">
<style>
:root{
  --mint:#bfe6d7;
  --mint-soft:#cde9de;
  --mint-deep:#a9dcc8;
  --btn-text:#244a3d;
  --ink:#1d1d1d;
  --body:#777;
  --ghost:#d9d9d9;
  --band:#ebebeb;
  --card:#f4f4f4;
  --footer:#333;
  --white:#fff;
}
*{margin:0;padding:0;box-sizing:border-box}
html,body{width:1200px;height:4800px;overflow:hidden}
body{position:relative;background:var(--white);font-family:"Lato",sans-serif;color:var(--ink)}
.abs{position:absolute}
.btn{position:absolute;background:var(--mint-soft);color:var(--btn-text);font-weight:700;font-size:14px;letter-spacing:.5px;padding:10px 16px;text-transform:uppercase;white-space:nowrap}

/* hero */
.hero{left:0;top:0;width:1200px;height:720px;overflow:hidden}
.hero-photo{position:absolute;inset:0;background:linear-gradient(180deg,#2f6f9e 0%,#5d9cc4 30%,#8fb7c6 42%,#c49a68 60%,#a9794b 100%)}
.hero-wave{position:absolute;left:0;bottom:0;width:1200px;height:160px}
.logo{font-family:"Lato",sans-serif;font-weight:400;letter-spacing:4px;font-size:30px;color:var(--white)}
.nav{left:420px;top:60px;display:flex;gap:16px;font-size:14px;font-weight:700;color:var(--white)}
.nav-cta{left:888px;top:48px;background:var(--mint-soft);color:var(--btn-text);font-weight:700;font-size:15px;padding:10px 18px}
.hero-title{left:0;width:1200px;top:308px;text-align:center;font-size:48px;font-weight:700;color:var(--white);text-shadow:0 2px 6px rgba(0,0,0,.25)}
.dots{left:566px;top:651px;display:flex;gap:5px}
.dots span{width:9px;height:9px;border:1.5px solid #bbb;border-radius:50%}
.dots span.on{background:#bbb}

/* section headings */
.heading{position:absolute;left:0;width:1200px;text-align:center}
.heading .ghost{position:absolute;left:0;width:100%;top:-10px;font-size:56px;font-weight:400;color:var(--ghost);letter-spacing:2px}
.heading .main{position:relative;font-size:40px;font-weight:700;color:var(--ink)}

/* services */
.svc-frame{position:absolute;background:var(--mint)}
.svc-photo{position:absolute}
.svc-title{font-size:22px;font-weight:400;color:var(--ink)}
.svc-sub{font-size:16px;color:#333;margin-top:8px}
.svc-text{font-size:13.5px;line-height:27px;color:var(--body);margin-top:20px;text-align:justify}

/* pricing */
.pricing-band{left:0;top:2217px;width:1200px;height:717px;background:var(--band)}
.card{position:absolute;top:2353px;width:238px;height:423px;background:var(--card);border:2px solid #e2e2e2}
.card-top{position:absolute;left:0;top:0;width:100%;height:180px;background:#dbece5}
.card-name{position:absolute;top:30px;width:100%;text-align:center;font-size:20px;color:#222}
.card-price{position:absolute;top:66px;width:100%;text-align:center;font-size:44px;color:#111}
.card-wave{position:absolute;left:0;top:150px;width:100%;height:40px}
.card-body{position:absolute;left:18px;right:14px;top:210px;font-size:14px;line-height:24px;color:#555}
.card-body ul{margin-top:10px;list-style:none;font-size:13px;line-height:27px;color:#888}
.card-body li::before{content:"";display:inline-block;width:4px;height:4px;background:#444;border-radius:50%;margin-right:4px;vertical-align:middle}
.card .btn{left:18px;top:366px}

/* about */
.about-title{left:620px;top:3090px;font-size:42px;font-weight:700}
.about-title .ghost{position:absolute;left:0;top:0;color:var(--ghost);font-weight:400;white-space:nowrap}
.about-title .main{position:relative;white-space:nowrap}

/* booking */
.booking-band{left:0;top:3512px;width:1200px;height:313px;background:var(--mint-soft)}
.booking-band .ghost{color:#b7dccd}
.booking-text{left:250px;width:700px;top:3640px;text-align:center;font-size:14.5px;line-height:28px;color:#777}

/* contact */
.map{position:absolute;top:4015px;width:480px;height:330px;background:linear-gradient(135deg,#e6e6e6,#d9d9d9);border:2px solid #e0e0e0}
.map-card{position:absolute;left:120px;width:240px;background:var(--white);text-align:center;color:#555;font-size:14px;line-height:26px;padding:14px 0}
.map-card b{display:block;font-weight:400;font-size:16px;color:#333;margin-bottom:2px}

/* footer */
.footer{left:0;top:4440px;width:1200px;height:360px}
.footer-links{left:0;width:1200px;top:4652px;text-align:center;font-size:14px;color:#ddd}
.footer-links span{margin:0 10px}
.footer-contact{left:0;width:1200px;top:4690px;display:flex;justify-content:center;align-items:center;gap:14px;color:#ddd;font-size:14px}
.icon-circle{width:28px;height:28px;border:1.5px solid #ccc;border-radius:50%;display:flex;align-items:center;justify-content:center}
.copyright{left:0;width:1200px;top:4743px;text-align:center;font-size:13px;color:#ddd}
</style>
</head>
<body>

<!-- Hero -->
<section class="abs hero">
  <div class="hero-photo" role="img" aria-label="Woman running along a sunlit beach at the water's edge"></div>
  <svg class="hero-wave" viewBox="0 0 1200 160" preserveAspectRatio="none">
    <path d="M0 120 Q600 250 1200 110 L1200 160 L0 160Z" fill="#bfe6d7"/>
    <path d="M0 60 Q600 230 1200 50 L1200 160 L0 160Z" fill="#fff"/>
    <path d="M0 60 Q600 230 1200 50 L1200 160 Q600 210 0 160Z" fill="#fff"/>
  </svg>
</section>
<div class="abs logo" style="left:110px;top:50px">FROSTLINE</div>
<nav class="abs nav"><span>Home</span><span>Services</span><span>About</span><span>Pricing</span><span>Online booking</span><span>Contact</span><span>Blog</span></nav>
<div class="abs nav-cta">MAKE APPOINTMENT</div>
<h1 class="abs hero-title">OPTIMAL PERFORMANCE &amp; RECOVERY</h1>
<div class="abs dots"><span></span><span></span><span class="on"></span><span></span><span></span></div>

<!-- Services -->
<div class="heading" style="top:820px"><div class="ghost">OUR SERVICES</div><div class="main">OUR SERVICES</div></div>

<div class="svc-frame" style="left:112px;top:950px;width:170px;height:145px"></div>
<div class="svc-frame" style="left:430px;top:1145px;width:170px;height:140px"></div>
<div class="svc-photo" role="img" aria-label="Client standing in a whole body cryotherapy chamber under blue light" style="left:130px;top:969px;width:448px;height:294px;background:linear-gradient(160deg,#6f7fd6,#3d55c4 55%,#8da0dd)"></div>
<div class="abs" style="left:669px;top:975px;width:418px">
  <div class="svc-title">Whole Body Cryotherapy</div>
  <div class="svc-sub">Relief &amp; rejuvenation for your entire body</div>
  <div class="svc-text">Whole Body Cryotherapy is a quick, non-invasive process that exposes your body to extreme cold up to -250F. This sudden drop in temperature increases circulation and pumps re-oxygenated, nutrient enriched</div>
</div>
<div class="btn" style="left:669px;top:1190px">Learn more</div>

<div class="abs" style="left:112px;top:1402px;width:440px">
  <div class="svc-title">Local Cryotherapy</div>
  <div class="svc-sub">Reduce pain, inflammation &amp; swelling in targeted areas</div>
  <div class="svc-text">Local cryotherapy acts as a higher intensity, more efficient form of “icing.” With the use of liquid nitrogen, the treatment delivers colder, more consistent temperatures, more effectively targeting the problem area.</div>
</div>
<div class="btn" style="left:112px;top:1617px">Learn more</div>
<div class="svc-frame" style="left:598px;top:1383px;width:170px;height:145px"></div>
<div class="svc-frame" style="left:918px;top:1575px;width:168px;height:145px"></div>
<div class="svc-photo" role="img" aria-label="Therapist applying a localised cold vapour treatment to a client's shoulder" style="left:618px;top:1401px;width:448px;height:294px;background:linear-gradient(100deg,#e9dccd 0%,#d8c3ad 35%,#2f3a56 55%,#e8ebef 100%)"></div>

<div class="svc-frame" style="left:112px;top:1774px;width:170px;height:145px"></div>
<div class="svc-frame" style="left:430px;top:1968px;width:170px;height:142px"></div>
<div class="svc-photo" role="img" aria-label="Client lying down receiving a cryo facial vapour treatment" style="left:130px;top:1792px;width:448px;height:295px;background:linear-gradient(180deg,#1d2f55 0%,#2c4372 45%,#c9d3df 70%,#f2f2f2 100%)"></div>
<div class="abs" style="left:669px;top:1798px;width:418px">
  <div class="svc-title">Cryo Facial</div>
  <div class="svc-sub">Slow down the aging process</div>
  <div class="svc-text">Cryo Facials apply pressurized liquid nitrogen vapors to the face, neck and scalp to help stimulate and improve the overall appearance of the skin. Regular treatments help stimulate the production of collagen, shrink pores,</div>
</div>
<div class="btn" style="left:669px;top:2013px">Learn more</div>

<!-- Pricing -->
<div class="abs pricing-band"></div>
<div class="heading" style="top:2268px"><div class="ghost">OUR PRICING</div><div class="main">OUR PRICING</div></div>

<div class="card" style="left:110px">
  <div class="card-top"></div>
  <div class="card-name">SINGLE</div><div class="card-price">$ 40</div>
  <svg class="card-wave" viewBox="0 0 238 40" preserveAspectRatio="none"><path d="M0 10 Q60 40 120 15 T238 10 L238 40 L0 40Z" fill="#f4f4f4"/><path d="M60 22 Q120 0 180 18" stroke="#bfe6d7" stroke-width="4" fill="none"/></svg>
  <div class="card-body">Nemo enim ipsam quia sit a aut odit aut fugit<ul><li>Sit amet</li><li>Consectetur</li><li>Adipisci velit,</li></ul></div>
  <div class="btn">Buy now</div>
</div>
<div class="card" style="left:356px">
  <div class="card-top" style="background:var(--mint-soft)"></div>
  <div class="card-name">10 PACK</div><div class="card-price">$ 380</div>
  <svg class="card-wave" viewBox="0 0 238 40" preserveAspectRatio="none"><path d="M0 10 Q60 40 120 15 T238 10 L238 40 L0 40Z" fill="#f4f4f4"/><path d="M60 22 Q120 0 180 18" stroke="#bfe6d7" stroke-width="4" fill="none"/></svg>
  <div class="card-body">Nemo enim ipsam quia sit a aut odit aut fugit<ul><li>Sit amet</li><li>Consectetur</li><li>Adipisci velit,</li></ul></div>
  <div class="btn">Buy now</div>
</div>
<div class="card" style="left:604px">
  <div class="card-top"></div>
  <div class="card-name">20 PACK</div><div class="card-price">$ 720</div>
  <svg class="card-wave" viewBox="0 0 238 40" preserveAspectRatio="none"><path d="M0 10 Q60 40 120 15 T238 10 L238 40 L0 40Z" fill="#f4f4f4"/><path d="M60 22 Q120 0 180 18" stroke="#bfe6d7" stroke-width="4" fill="none"/></svg>
  <div class="card-body">Nemo enim ipsam quia sit a aut odit aut fugit<ul><li>Sit amet</li><li>Consectetur</li><li>Adipisci velit,</li></ul></div>
  <div class="btn">Buy now</div>
</div>
<div class="card" style="left:850px">
  <div class="card-top"></div>
  <div class="card-name">MONTHLY*</div><div class="card-price">$ 400</div>
  <svg class="card-wave" viewBox="0 0 238 40" preserveAspectRatio="none"><path d="M0 10 Q60 40 120 15 T238 10 L238 40 L0 40Z" fill="#f4f4f4"/><path d="M60 22 Q120 0 180 18" stroke="#bfe6d7" stroke-width="4" fill="none"/></svg>
  <div class="card-body">Nemo enim ipsam quia sit a aut odit aut fugit<ul><li>Sit amet</li><li>Consectetur</li><li>Adipisci velit,</li></ul></div>
  <div class="btn">Buy now</div>
</div>
<div class="btn" style="left:517px;top:2828px;padding:10px 22px">Book a session</div>

<!-- About -->
<div class="abs" style="left:133px;top:3027px;width:398px;height:392px;border-radius:50%;background:var(--mint)"></div>
<div class="abs" role="img" aria-label="Whole body cryotherapy cabin in white and blue" style="left:110px;top:3027px;width:392px;height:392px;border-radius:50%;background:radial-gradient(circle at 50% 45%,#e2e2e2,#b9b9b9)"></div>
<div class="abs about-title"><div class="ghost" style="left:0">ABOUT <span style="color:var(--ghost)">US</span></div><div class="main">ABOUT <span style="color:transparent">US</span></div></div>
<div class="abs" style="left:620px;top:3160px;width:468px;font-size:14px;line-height:26px;color:var(--body);text-align:justify">Originally invented by doctors as a powerful anti-inflammatory tool, cryotherapy is a quick, noninvasive process that exposes your body to extreme cold of up to -250°F. This sudden drop in temperature increases circulation and pumps</div>
<div class="btn" style="left:620px;top:3300px">Learn more</div>

<!-- Online booking -->
<div class="abs booking-band"></div>
<div class="heading" style="top:3562px"><div class="ghost">ONLINE BOOKING</div><div class="main">ONLINE BOOKING</div></div>
<div class="abs booking-text">Neque porro quisquam est, qui dolorem ipsum quia dolor sit amet, consectetur, adipisci velit, sed quia non numquam eius modi tempora incidunt ut labore et dolore magnam</div>
<div class="btn" style="left:532px;top:3714px;background:#f3f3f3;padding:11px 24px">Book now</div>

<!-- Contact -->
<div class="heading" style="top:3918px"><div class="ghost">CONTACT US</div><div class="main">CONTACT US</div></div>
<div class="map" role="img" aria-label="Street map of the Westbrook studio area" style="left:110px">
  <div class="map-card" style="top:26px"><b>WESTBROOK</b>12 Harbor Lane<br>2nd Floor</div>
  <div class="map-card" style="top:196px"><b>HOURS</b>Mon - Fri 6:30 am - 8:00 pm<br>Saturday 8:00 am - 1:00 pm<br>Sunday Closed</div>
</div>
<div class="map" role="img" aria-label="Street map of the Fairhaven studio area" style="left:609px">
  <div class="map-card" style="top:26px"><b>FAIRHAVEN</b>410 Mill Street<br>3rd Floor</div>
  <div class="map-card" style="top:196px"><b>HOURS</b>Mon - Fri 6:00 am - 7:00 pm<br>Saturday Closed<br>Sunday Closed</div>
</div>

<!-- Footer -->
<svg class="abs footer" viewBox="0 0 1200 360" preserveAspectRatio="none"><path d="M0 0 Q600 110 1200 0 L1200 360 L0 360Z" fill="#333"/></svg>
<div class="abs logo" style="left:0;width:1200px;text-align:center;top:4588px;color:#ccc;font-size:28px">FROSTLINE</div>
<div class="abs footer-links"><span>Home</span>|<span>Services</span>|<span>About</span>|<span>Pricing</span>|<span>Online Booking</span>|<span>Contact</span>|<span>Blog</span></div>
<div class="abs footer-contact">
  <div class="icon-circle"><svg width="14" height="14" viewBox="0 0 24 24"><path d="M6.6 10.8a15 15 0 006.6 6.6l2.2-2.2a1 1 0 011-.25 11 11 0 003.6.6 1 1 0 011 1V20a1 1 0 01-1 1A17 17 0 013 4a1 1 0 011-1h3.5a1 1 0 011 1 11 11 0 00.6 3.6 1 1 0 01-.25 1z" fill="#ccc"/></svg></div>
  <span style="margin-right:40px">555-014-2290</span>
  <div class="icon-circle"><svg width="14" height="14" viewBox="0 0 24 24"><rect x="3" y="6" width="18" height="12" fill="none" stroke="#ccc" stroke-width="2"/><path d="M3 6l9 7 9-7" fill="none" stroke="#ccc" stroke-width="2"/></svg></div>
  <span style="margin-right:40px">hello@frostline-studio.com</span>
  <div class="icon-circle"></div>
  <div class="icon-circle"></div>
</div>
<div class="abs copyright">© 2019 Frostline. All Rights Reserved</div>

</body>
</html>
```